Business Card Design Project

Business Card design based on logo.
Updates

I need business card, letterhead, envelope, and if possible, Powerpoint slide template.

On front of business card: Just logo- and  my name and title:  Harriet Lindqvist, Principal

On reverse-logo and the rest of the contact info:

4871 Quarry Lane
Fenwick, CA 95724
650-318-2764
hl@brackenstudyworks.example

On letterhead-Just logo at top, at bottom  the rest-very small along the bottom

On PPT slide-just the logo.

I also want to try a few other colors-I like lime/dark grey (not black) but would like to try Sienna, maybe also indigo or bright blue-green.

I forgot to add-

On the business card-switch to vertical on reverse side and put:

Reverse side-switch to vertical and list:

Harriet Lindqvist
Principal
Bracken Study Works, LLC

650-318-2764

4871 Quarry Lane
Fenwick, CA 95724

Harriet Lindqvist
Principal

650-318-2764

4871 Quarry Lane
Fenwick, CA 95724

I have another project at the same time-for Stationery. Feel free to submit to that one also.

That one includes letterhead, envelope, PPT slide, folder cover sheet-HL

Industry/Entity Type

Business

Requirements
Must have
• Must use logo-preferably lime green version-with gray, not black or just 2-tone -logo on colored background.

```html
<!DOCTYPE html>
<html lang="en">
<head>
<meta charset="utf-8">
<title>Bracken Study Works – Business Card</title>
<link rel="stylesheet" href="https://fonts.googleapis.com/css2?family=Lato:wght@400;700&display=swap">
<style>
  :root {
    --lime: #9bba2f;
    --lime-dark: #8aa827;
    --charcoal: #4a4a4c;
    --ink: #555557;
    --paper: #ffffff;
    --backdrop: #ececec;
    --rule: #6b6b6b;
  }
  * { margin: 0; padding: 0; box-sizing: border-box; }
  html, body {
    width: 1200px;
    height: 900px;
    overflow: hidden;
    background: var(--backdrop);
    font-family: "Lato", Arial, sans-serif;
  }
  .canvas { position: relative; width: 1200px; height: 900px; }

  /* Front of card */
  .card-front {
    position: absolute;
    left: 134px; top: 300px;
    width: 532px; height: 296px;
    background: var(--lime);
    display: flex;
    flex-direction: column;
    align-items: center;
    justify-content: center;
    gap: 22px;
  }
  .brand-dot {
    width: 46px; height: 46px;
    border-radius: 50%;
    background: var(--paper);
  }
  .brand-name {
    font-weight: 400;
    font-size: 40px;
    letter-spacing: 6px;
    color: var(--charcoal);
    text-transform: uppercase;
    text-align: center;
    line-height: 1.15;
  }

  /* Back of card */
  .card-back {
    position: absolute;
    left: 766px; top: 182px;
    width: 296px; height: 532px;
    background: var(--paper);
    color: var(--ink);
  }
  .holder { position: absolute; left: 20px; top: 70px; }
  .holder-name { font-weight: 400; font-size: 23px; letter-spacing: 0.3px; line-height: 1.1; margin-bottom: 2px; }
  .holder-role, .holder-firm { font-size: 15px; line-height: 20px; }
  .divider {
    position: absolute; left: 18px; top: 157px;
    width: 239px; height: 1px; background: var(--rule);
  }
  .contact { position: absolute; left: 18px; list-style: none; font-size: 15px; line-height: 20px; }
  .contact li { display: flex; align-items: flex-start; gap: 8px; }
  .contact svg { flex: none; margin-top: 3px; }
  .contact-lines { top: 200px; }
  .contact-address { top: 268px; }
  .back-brand {
    position: absolute; left: 0; right: 0; top: 398px;
    display: flex; flex-direction: column; align-items: center; gap: 12px;
  }
  .back-brand .brand-dot { width: 34px; height: 34px; background: var(--lime); }
  .back-brand .brand-name { font-size: 17px; letter-spacing: 2px; color: var(--lime); }
  .website {
    position: absolute; left: 0; right: 0; top: 496px;
    text-align: center; font-size: 15px; color: var(--ink);
  }
  .website .domain { color: var(--lime-dark); }
</style>
</head>
<body>
<main class="canvas">

  <section class="card-front" aria-label="Business card front">
    <span class="brand-dot" aria-hidden="true"></span>
    <p class="brand-name">Bracken<br>Study Works</p>
  </section>

  <section class="card-back" aria-label="Business card back">
    <div class="holder">
      <h1 class="holder-name">HARRIET LINDQVIST</h1>
      <p class="holder-role">Principal</p>
      <p class="holder-firm">Bracken Study Works, LLC</p>
    </div>
    <div class="divider"></div>

    <ul class="contact contact-lines">
      <li>
        <svg width="14" height="14" viewBox="0 0 14 14" aria-hidden="true">
          <rect x="1" y="1" width="12" height="12" rx="1.5" fill="none" stroke="#9bba2f" stroke-width="1.6"/>
          <rect x="3.5" y="3" width="2.5" height="8" fill="#9bba2f"/>
          <rect x="7.5" y="4" width="3.5" height="2" fill="#9bba2f"/>
          <rect x="7.5" y="8" width="3.5" height="2" fill="#9bba2f"/>
        </svg>
        <span>650-318-2764</span>
      </li>
      <li>
        <svg width="14" height="14" viewBox="0 0 14 14" aria-hidden="true">
          <rect x="1" y="3" width="12" height="9" fill="none" stroke="#9bba2f" stroke-width="1.4"/>
          <path d="M1 3 L7 8 L13 3" fill="none" stroke="#9bba2f" stroke-width="1.4"/>
        </svg>
        <span>hl@brackenstudyworks.example</span>
      </li>
    </ul>

    <ul class="contact contact-address">
      <li>
        <svg width="14" height="16" viewBox="0 0 14 16" aria-hidden="true">
          <path d="M7 1 C3.8 1 2 3.3 2 5.7 C2 9 7 14 7 14 C7 14 12 9 12 5.7 C12 3.3 10.2 1 7 1 Z" fill="#9bba2f"/>
          <circle cx="7" cy="5.8" r="1.8" fill="#fff"/>
        </svg>
        <span>4871 Quarry Lane<br>Fenwick, CA 95724</span>
      </li>
    </ul>

    <div class="back-brand">
      <span class="brand-dot" aria-hidden="true"></span>
      <p class="brand-name">Bracken Study Works</p>
    </div>
    <p class="website">www.<span class="domain">brackenstudyworks</span>.example</p>
  </section>

</main>
</body>
</html>
```